Counseling Practice Business Card

I need a professional looking business card incorporating my new logo that was just completed. Card needs to incorporate my name and title, description of my specialty, my address, my phone number, my fax number, my email and my website URL. I need to be able to choose design on/with different paper colors and textures.
I do not have a lot of business card ideas so I am open to anything but I want bold,sharp, clear card without additional designs other than my logo (see attached file info). I am open to different color backgrounds or paper colors including black. I do not like traditional brackets around area codes in phone number or dashes between numbers in phone number. Am open to other ways of presenting including periods between numbers as appropriate. I do not know enough to know what I like yet but I want card to coordinate and work together with my logo. My practice emphasizes natural mental health interventions so any use of color (with background paper color or the blue and green in my logo) that elicits nature is nice. In addition to black, any natural brown or wood looking background might be desirable also. Most of the offerings so far look very similar and boring.

Target Market(s)

Potential therapy clients and other professionals

Contact Information for Business Card

Card information:
Gerald M. Whitcombe, Ph.D.
Licensed Clinical Psychologist
Integrative Health Coach
4812 Marlowe Ridge Blvd SE
Suite 310
Duluth, GA 30096
770.415.2983 phone
770.581.4096 fax
drgeraldwhitcombe@quillmarsh.net
brightfernwellness.net

Font styles to use
Serif
Sans Serif
Other font styles liked:
• anything that you think looks crisp, clear and easily readable

Requirements
Must have
• Any color used should coordinate with my logo design (see attached files).
• Card should be printed horizontally so top and bottom are longest sides of rectangle.
• Background color or paper color should complement and highlight logo. Do not like a white background. black, grey, brown or any color my logo would blend well with.
Nice to have
• I would like designer to utilize color to highlight letters/name or phone-fax-web symbols.
• Bottom edge of card could be highlighted if appropriate to an idea.
Should not have
• I would NOT want the card to have a pure white background at all.
• No clear cards.
• Cards should be oriented with long sides on bottom and top, NOT sides. DO NOT LIKE THIS THIN TALL ORIENTATION.

```html
<!DOCTYPE html>
<html lang="en">
<head>
<meta charset="utf-8">
<title>Brightfern Wellness – Business Card</title>
<link rel="stylesheet" href="https://fonts.googleapis.com/css2?family=Source+Sans+3:wght@400;600&family=PT+Sans+Narrow&display=swap">
<style>
  :root {
    --page: #ffffff;
    --wood-light: #b9b0a4;
    --wood-mid: #a89e91;
    --wood-dark: #948a7e;
    --brand-blue: #3b7fc2;
    --brand-green: #2f8a3f;
    --icon-ink: #ffffff;
  }
  * { margin: 0; padding: 0; box-sizing: border-box; }
  html, body {
    width: 1200px; height: 1200px; overflow: hidden;
    background: var(--page);
  }
  .card {
    position: absolute; left: 200px; top: 372px;
    width: 800px; height: 457px; overflow: hidden;
    font-family: "Source Sans 3", sans-serif;
    color: var(--brand-blue);
  }
  .card-texture {
    position: absolute; inset: 0;
    background: linear-gradient(175deg, var(--wood-light) 0%, var(--wood-mid) 45%, var(--wood-light) 70%, var(--wood-dark) 100%);
  }
  .brand {
    position: absolute; left: 44px; top: 52px; width: 300px;
    text-align: center; color: var(--brand-blue); font-weight: 400;
  }
  .brand-name { display: block; font-size: 56px; line-height: 1; letter-spacing: -0.5px; }
  .brand-tag { display: block; font-size: 20px; letter-spacing: 11px; margin-top: 8px; }
  .practitioner { position: absolute; left: 44px; top: 182px; }
  .practitioner-name { font-size: 29px; font-weight: 400; line-height: 1.2; }
  .practitioner-role {
    font-family: "PT Sans Narrow", sans-serif;
    font-size: 19px; line-height: 27px; text-transform: uppercase;
    margin-top: 8px;
  }
  .swoosh { position: absolute; left: 0; top: 318px; width: 800px; height: 70px; }
  .contact-list { position: absolute; left: 0; top: 0; width: 800px; list-style: none; }
  .contact-item {
    position: absolute; right: 44px;
    display: flex; align-items: flex-start; gap: 18px;
    font-size: 19px; line-height: 25px; text-align: right;
  }
  .contact-item .icon {
    width: 29px; height: 29px; flex: none;
    background: var(--brand-green);
    display: flex; align-items: center; justify-content: center;
    margin-top: -2px;
  }
  .contact-item .icon svg { width: 19px; height: 19px; }
  .contact-web { color: var(--brand-green); }
</style>
</head>
<body>
  <div class="card">
    <div class="card-texture" role="img" aria-label="Brushed wood grain paper texture"></div>

    <div class="brand">
      <span class="brand-name">Brightfern</span>
      <span class="brand-tag">WELLNESS</span>
    </div>

    <div class="practitioner">
      <h1 class="practitioner-name">Gerald M. Whitcombe, Ph.D.</h1>
      <p class="practitioner-role">Licensed Clinical Psychologist<br>Integrative Health Coach</p>
    </div>

    <svg class="swoosh" viewBox="0 0 800 70" preserveAspectRatio="none" aria-hidden="true">
      <path d="M0 26 Q380 -10 800 28 L800 44 Q380 10 0 70 Z" fill="var(--brand-blue)"/>
    </svg>

    <ul class="contact-list">
      <li class="contact-item" style="top:60px">
        <span>770.415.2983</span>
        <span class="icon"><svg viewBox="0 0 20 20" fill="none" stroke="var(--icon-ink)" stroke-width="1.8" stroke-linecap="round"><path d="M7 3 L5 4 Q4 10 7 16 L9 17 L10 14 L8 12 Q7 10 8 8 L10 7 Z"/></svg></span>
      </li>
      <li class="contact-item" style="top:100px">
        <span>770.581.4096</span>
        <span class="icon"><svg viewBox="0 0 20 20" fill="none" stroke="var(--icon-ink)" stroke-width="1.5"><rect x="2" y="4" width="16" height="12"/><line x1="2" y1="8" x2="18" y2="8"/></svg></span>
      </li>
      <li class="contact-item" style="top:140px">
        <span>drgeraldwhitcombe@quillmarsh.net</span>
        <span class="icon"><svg viewBox="0 0 20 20" fill="none" stroke="var(--icon-ink)" stroke-width="1.5"><rect x="2" y="4" width="16" height="12"/><path d="M2 4 L10 11 L18 4"/></svg></span>
      </li>
      <li class="contact-item" style="top:180px">
        <span>4812 Marlowe Ridge Blvd SE Suite 310<br>Duluth, GA 30096</span>
        <span class="icon"><svg viewBox="0 0 20 20" fill="none" stroke="var(--icon-ink)" stroke-width="1.5"><path d="M10 18 L5 10 A5.5 5.5 0 1 1 15 10 Z"/><circle cx="10" cy="7.5" r="2"/></svg></span>
      </li>
      <li class="contact-item contact-web" style="top:404px">
        <span>brightfernwellness.net</span>
        <span class="icon"><svg viewBox="0 0 20 20" fill="none" stroke="var(--icon-ink)" stroke-width="1.3"><circle cx="10" cy="10" r="7.5"/><ellipse cx="10" cy="10" rx="3.2" ry="7.5"/><line x1="2.5" y1="10" x2="17.5" y2="10"/><line x1="4" y1="6" x2="16" y2="6"/><line x1="4" y1="14" x2="16" y2="14"/></svg></span>
      </li>
    </ul>
  </div>
</body>
</html>
```